Business card design for new eCommerce site focusing on integrity and strong businsess tactics

We need a business card that will stand out and be memorable. Something with color that matches our company logo colors. Think high end version of Pactivo. There are 2 logos provided. The parent company is called Amber Ledge Partners and we are presenting a new and very exciting eCommerce site called BrightHarborTrade.example.

Target Market(s)

Our target markets are in the Activities, Food and Beverage, Health and Beauty

Industry/Entity Type

Marketing

Contact Information for Business Card

We have 4 members that need cards...I will provide all info to the winner of the design contest
Business Address is
4870 West 63rd Avenue, Suite C207
Phoenix AZ 85731

Font styles to use
Serif
Sans Serif

Colors

Designer to choose colors to be used in the design.

Requirements
Must have
• The card must be memorable...should be unique in design but must exude integrity and be playful .
• I have provided several colors or our parent company...please feel free to use which ever
Nice to have
• I will leave this up to you. Feel free to use other images of your choosing that wraps around our client.....Activities, Dining, Health, Beauty
Should not have
• just dont be boring

```html
<!DOCTYPE html>
<html lang="en">
<head>
<meta charset="utf-8">
<title>Amber Ledge Partners – Business Card</title>
<link href="https://fonts.googleapis.com/css2?family=Nunito:wght@800&family=Open+Sans:wght@400;600;700&display=swap" rel="stylesheet">
<style>
  :root{
    --page:#ecedef;
    --sky:#46c5e2;
    --ocean:#2a6fb0;
    --leaf:#7cc242;
    --stripe:#2f7cc0;
    --brand-blue:#2a72b5;
    --ink:#3a3f45;
    --white:#ffffff;
    --shadow:0 14px 30px rgba(0,0,0,.18);
  }
  *{box-sizing:border-box;margin:0;padding:0}
  html,body{width:1200px;height:900px;overflow:hidden}
  body{background:var(--page);font-family:"Open Sans",sans-serif;position:relative}

  .card{position:absolute;left:280px;width:640px;height:366px;border-radius:4px;overflow:hidden;box-shadow:var(--shadow)}
  .card--front{top:60px;background:linear-gradient(100deg,var(--sky) 0%,var(--ocean) 62%,var(--ocean) 100%);color:var(--white);text-align:center}
  .card--back{top:474px;background:var(--white)}

  .front__mark{display:block;margin:88px auto 18px}
  .front__name{font-family:"Nunito",sans-serif;font-weight:800;font-size:40px;letter-spacing:.2px;line-height:1}
  .front__sub{margin-top:4px;font-size:15px;letter-spacing:6px;font-weight:400}
  .front__web{margin-top:28px;font-size:14px;letter-spacing:4px;font-weight:600}

  .back__wave{position:absolute;inset:0}
  .back__art{position:absolute;left:140px;top:50px;width:130px;height:110px;border-radius:50%;
    background:radial-gradient(circle at 40% 45%,rgba(124,194,66,.35),rgba(47,124,192,.12) 70%,rgba(255,255,255,0) 100%)}
  .brand{position:absolute;right:34px;top:40px;text-align:left}
  .brand__row{display:flex;align-items:center;gap:10px}
  .brand__dot{width:22px;height:22px;border-radius:50%;background:var(--leaf)}
  .brand__name{font-family:"Open Sans",sans-serif;font-weight:700;font-size:22px;color:var(--brand-blue)}
  .brand__tag{margin:6px 0 0 32px;font-size:12.5px;color:var(--ink);letter-spacing:.6px}

  .contact{position:absolute;left:30px;top:168px;color:var(--white);font-size:13.5px;line-height:18px}
  .contact__name{font-weight:700;text-transform:uppercase;font-size:14.5px}
  .contact__role{margin-bottom:12px}
  .contact__address{margin-bottom:6px}
  .contact__list{list-style:none}
  .contact__list li{display:flex;align-items:center;gap:8px}
  .contact__list svg{width:12px;height:12px;flex:none}
</style>
</head>
<body>

<section class="card card--front" aria-label="Card front">
  <svg class="front__mark" width="40" height="40" viewBox="0 0 40 40" aria-hidden="true">
    <circle cx="20" cy="20" r="17" fill="none" stroke="#fff" stroke-width="3"/>
  </svg>
  <h1 class="front__name">Amber Ledge</h1>
  <p class="front__sub">Partners</p>
  <p class="front__web">www.brightharbortrade.example</p>
</section>

<section class="card card--back" aria-label="Card back">
  <svg class="back__wave" viewBox="0 0 640 366" preserveAspectRatio="none" aria-hidden="true">
    <path d="M0,138 C120,86 238,148 300,236 C342,296 402,344 505,366 L480,366 C385,350 330,305 290,250 C230,165 120,100 0,150 Z" fill="var(--stripe)"/>
    <path d="M0,150 C120,100 230,165 290,250 C330,305 385,350 480,366 L0,366 Z" fill="var(--leaf)"/>
  </svg>
  <div class="back__art" role="img" aria-label="Illustration of a figure with leaves rising from the wave"></div>

  <div class="brand">
    <div class="brand__row">
      <span class="brand__dot"></span>
      <span class="brand__name">BrightHarborTrade.example</span>
    </div>
    <p class="brand__tag">Outings-Meals-Wellness-Style</p>
  </div>

  <div class="contact">
    <p class="contact__name">Dana Whitfield</p>
    <p class="contact__role">CEO/FOUNDER</p>
    <p class="contact__address">4870 West 63rd Avenue<br>Suite C207<br>Phoenix AZ 85731</p>
    <ul class="contact__list">
      <li><svg viewBox="0 0 12 12"><path d="M2 1h2.5l1 3-1.5 1a6 6 0 0 0 3 3l1-1.5 3 1V11C6 11 1 6 1 2z" fill="#fff"/></svg>555 014 2207</li>
      <li><svg viewBox="0 0 12 12"><rect x="3" y="0.5" width="6" height="11" rx="1" fill="none" stroke="#fff" stroke-width="1.3"/><circle cx="6" cy="9.5" r=".8" fill="#fff"/></svg>555 019 3318</li>
      <li><svg viewBox="0 0 12 12"><rect x="0.7" y="2.2" width="10.6" height="7.6" fill="none" stroke="#fff" stroke-width="1.3"/><path d="M1 2.6l5 4 5-4" fill="none" stroke="#fff" stroke-width="1.2"/></svg>dana@brightharbortrade.example</li>
      <li><svg viewBox="0 0 12 12"><circle cx="6" cy="6" r="5" fill="none" stroke="#fff" stroke-width="1.2"/><path d="M1 6h10M6 1c-2.5 3-2.5 7 0 10M6 1c2.5 3 2.5 7 0 10" fill="none" stroke="#fff" stroke-width="1"/></svg>www.brightharbortrade.example</li>
    </ul>
  </div>
</section>

</body>
</html>
```